Letterhead for a German Distribution/Manufacturing Company

We need a professional Letterhead in a unique Design.
not to playful.
The Letterhead has to show show that we are a international company with headquater in Germany.
all details like adress, Vat Tax Number, Bank Accout, Eori, email, Company number has to be on the Letterhead.
for example use: VAT TAX DE5470318 Bank Account: Kestrel Bank IBAN DE412058731ß204683 Swift: MORV0417352 EORI 3150428697 Company Number: HRB 51806 Adress: VOLMINTA UG Ahornweg 7 Postal Code 06384 City Lindenfeld Country: Germany Email: info@volminta-example.com
the design can be colored but doesnt have to be
Industry/Entity Type
Manufacturing and international distribution
Requirements
Must have
- show that we are a international company with headquater in Germany. our company infos and logo

```html
<!DOCTYPE html>
<html lang="en">
<head>
<meta charset="utf-8">
<title>VOLMINTA Letterhead</title>
<link href="https://fonts.googleapis.com/css2?family=Poppins:wght@300;400;500;600&display=swap" rel="stylesheet">
<style>
  :root {
    --page-bg: #efefef;
    --paper: #ffffff;
    --band: #4a4a4a;
    --ink: #1f1f1f;
    --body-ink: #4a4a4a;
    --accent: #f26b45;
    --flag-black: #1a1a1a;
    --flag-red: #dd1f26;
    --flag-gold: #ffcc00;
  }
  html, body {
    margin: 0;
    width: 1200px;
    height: 2444px;
    overflow: hidden;
    background: var(--page-bg);
    font-family: "Poppins", sans-serif;
  }
  .letter {
    position: absolute;
    left: 50px;
    top: 510px;
    width: 893px;
    height: 1155px;
    background: linear-gradient(180deg, #f7f7f7 0%, var(--paper) 30%, var(--paper) 100%);
    box-shadow: 0 10px 40px rgba(0,0,0,.12);
    transform: scale(1.2318);
    transform-origin: top left;
    overflow: hidden;
  }
  .world-map {
    position: absolute; left: 0; top: 0; width: 640px; height: 180px;
    background: radial-gradient(ellipse at 40% 40%, rgba(200,200,200,.35), rgba(230,230,230,0) 70%);
  }
  .header-shape { position: absolute; left: 0; top: 0; width: 893px; height: 170px; }
  .brand {
    position: absolute; left: 45px; top: 60px;
    display: flex; align-items: center; gap: 14px;
    font-size: 44px; font-weight: 400; color: var(--ink); letter-spacing: -0.5px;
  }
  .brand-dot { width: 54px; height: 54px; border-radius: 50%; background: var(--ink); }
  .tagline {
    position: absolute; left: 525px; top: 56px;
    display: flex; align-items: center; gap: 18px;
    color: #fff; font-weight: 500; font-size: 17.5px; line-height: 21px;
  }
  .germany-map {
    position: absolute; left: 410px; top: 650px; width: 440px; height: 360px;
    background: linear-gradient(160deg, rgba(60,60,60,.06) 0%, rgba(221,31,38,.12) 45%, rgba(255,204,0,.12) 80%);
    border-radius: 40% 30% 35% 45%;
  }
  .greeting {
    position: absolute; left: 45px; top: 214px; margin: 0;
    color: var(--accent); font-size: 27px; font-weight: 500;
  }
  .body-copy {
    position: absolute; left: 45px; top: 273px; width: 805px;
    color: var(--body-ink); font-size: 14.6px; line-height: 17.6px; font-weight: 400;
  }
  .body-copy p { margin: 0 0 17px; }
  .closing { position: absolute; left: 46px; top: 794px; font-size: 14px; font-weight: 500; color: var(--ink); }
  .signature-mark {
    position: absolute; left: 47px; top: 840px; width: 250px; height: 75px;
    background: linear-gradient(90deg, rgba(40,40,40,.08), rgba(40,40,40,.02));
  }
  .signature-line { position: absolute; left: 46px; top: 921px; width: 278px; height: 1.5px; background: var(--ink); }
  .signature-label { position: absolute; left: 46px; top: 928px; font-size: 14px; font-weight: 500; color: var(--ink); }
  .footer-rule { position: absolute; left: 45px; top: 1017px; width: 780px; height: 1.5px; background: var(--ink); }
  .pin { position: absolute; left: 804px; top: 964px; }
  .footer { position: absolute; top: 1034px; left: 0; width: 893px; font-size: 12.6px; line-height: 16px; font-weight: 500; color: var(--ink); }
  .footer-col { position: absolute; top: 0; }
  .footer-col .label { color: var(--accent); }
  .footer-col .gap { margin-top: 7px; }
  .col-vat { left: 79px; top: 6px; }
  .col-swift { left: 287px; top: 4px; }
  .col-eori { left: 492px; top: 4px; }
  .col-company { left: 671px; top: 0; }
  .col-company .email { color: var(--accent); font-weight: 600; }
</style>
</head>
<body>
  <div class="letter">
    <div class="world-map" role="img" aria-label="Faint grey world map behind the header"></div>

    <svg class="header-shape" viewBox="0 0 893 170" aria-hidden="true">
      <polygon points="417,0 893,0 893,145 492,145" fill="var(--band)"/>
      <polygon points="440,78 446,75 492,155 893,155 893,161 486,161" fill="var(--ink)"/>
    </svg>

    <div class="brand"><span class="brand-dot"></span>VOLMINTA</div>

    <div class="tagline">
      <svg width="58" height="38" viewBox="0 0 58 38" aria-hidden="true">
        <rect x="0" y="0" width="58" height="12.7" fill="var(--flag-black)"/>
        <rect x="0" y="12.7" width="58" height="12.7" fill="var(--flag-red)"/>
        <rect x="0" y="25.4" width="58" height="12.6" fill="var(--flag-gold)"/>
      </svg>
      <span>INTERNATIONAL COMPANY,<br>HEADQUARTER IN GERMANY</span>
    </div>

    <div class="germany-map" role="img" aria-label="Faint map of Germany in flag colours"></div>

    <h1 class="greeting">Dear Mr Brandt</h1>

    <div class="body-copy">
      <p>We are a German Based International Company. The reason we founded this company was to create a direct and easy way for Manufacturing Companies to start selling their Products directly on Marketplaces in Europe.</p>
      <p>Contrary to popular belief, Lorem Ipsum is not simply random text. It has roots in a piece of classical Latin literature from 45 BC, making it over 2000 years old. Edwin Harlowe, a Latin professor at Wexford Hill College in Ohio, looked up one of the more obscure Latin words, consectetur, from a Lorem Ipsum passage, and going through the cites of the word in classical literature, discovered the undoubtable source. Lorem Ipsum comes from sections 1.10.32 and 1.10.33 of "de Finibus Bonorum et Malorum" (The Extremes of Good and Evil) by Aulus Venter, written in 45 BC. This book is a treatise on the theory of ethics, very popular during the Renaissance. The first line of Lorem Ipsum, "Lorem ipsum dolor sit amet..", comes from a line in section 1.10.32.</p>
      <p>The standard chunk of Lorem Ipsum used since the 1500s is reproduced below for those interested. Sections 1.10.32 and 1.10.33 from "de Finibus Bonorum et Malorum" by Aulus Venter are also reproduced in their exact original form, accompanied by English versions from the 1914 translation by H. Corwell.</p>
      <p>Lorem Ipsum comes from sections 1.10.32 and 1.10.33 of "de Finibus Bonorum et Malorum" (The Extremes of Good and Evil) by Aulus Venter, written in 45 BC. This book is a treatise on the theory of ethics, very popular during the Renaissance. The first line of Lorem Ipsum, "ipsum dolor sit amet..", comes from a line in section 1.10.32.</p>
      <p>Sections 1.10.32 and 1.10.33 from "de Finibus Bonorum et Malorum" by Aulus Venter are also reproduced in their exact original form, accompanied by English versions from the 1914 translation by H. Corwell.</p>
      <p>Through our own 13.000sqm sized company and about 250 well educated Employees in Pakistan we are also able to provide Company’s the opportunity into easy private labeling and producing their own products. Small and high quantities are possible. The production line and process is overseen &amp; under direct control by our German Headquarter so High quality and best customer service are our standard.</p>
    </div>

    <div class="closing">Sincerely Your,</div>
    <div class="signature-mark" role="img" aria-label="Handwritten signature of Lena Marquardt"></div>
    <div class="signature-line"></div>
    <div class="signature-label">Signature</div>

    <div class="footer-rule"></div>
    <svg class="pin" width="42" height="60" viewBox="0 0 42 60" aria-hidden="true">
      <path d="M21 59 L7 33 A19 19 0 1 1 35 33 Z" fill="#5a5a5a"/>
      <circle cx="21" cy="20" r="13" fill="var(--flag-red)"/>
      <path d="M8 20 A13 13 0 0 1 34 20 L34 15 A13 13 0 0 0 8 15 Z" fill="var(--flag-black)"/>
      <path d="M8.5 24 L33.5 24 A13 13 0 0 1 8.5 24 Z" fill="var(--flag-gold)"/>
    </svg>

    <div class="footer">
      <div class="footer-col col-vat">
        <div><span class="label">VAT TAX</span> DE5470318</div>
        <div class="gap label">Bank Account</div>
        <div>Kestrel Bank IBAN</div>
        <div>DE412058731ß204683</div>
      </div>
      <div class="footer-col col-swift">
        <div><span class="label">Swift</span> MORV0417352</div>
        <div class="gap label">Address</div>
        <div>VOLMINTA UG Ahornweg 7 Postal Code 06384</div>
        <div>City Lindenfeld &nbsp;Country: Germany</div>
      </div>
      <div class="footer-col col-eori">
        <div><span class="label">EORI</span> 3150428697</div>
      </div>
      <div class="footer-col col-company">
        <div>Company Number</div>
        <div>HRB 51806</div>
        <div class="gap">Email</div>
        <div class="email">info@volminta-example.com</div>
      </div>
    </div>
  </div>
</body>
</html>
```